VFX Company Business Card Design Project

The Kestrel Works is a decentralized Visual Effects Studio servicing the television and feature film industries.
Project Brief:
Take our logo that was previously designed on Pencil Harbor and make a double sided business card.
Requirements:
- Card MUST be double sided.
- Front of card MUST have the yellow part of our logo against the dark grey background.
- Back of card is completely up to the designer.
- Back of card must include the complete company logo.
Please follow these File Preparation guidelines:
http://printnook.ca/infopage?file=filetype_en&s=PrintNook_new&lang=en
Business

```html
<!DOCTYPE html>
<html lang="en">
<head>
<meta charset="utf-8">
<title>The Kestrel Works – Business Card</title>
<link rel="stylesheet" href="https://fonts.googleapis.com/css2?family=PT+Sans:wght@400;700&display=swap">
<style>
  :root {
    --stage: #dfe3e6;
    --card-yellow: #ffcc26;
    --card-dark: #3a3a3a;
    --ink: #2f2f2f;
    --white: #ffffff;
    --accent-yellow: #f7c928;
  }
  * { box-sizing: border-box; margin: 0; padding: 0; }
  html, body {
    width: 1200px;
    height: 960px;
    overflow: hidden;
    background: var(--stage);
    font-family: "PT Sans", Arial, sans-serif;
  }
  .sheet {
    width: 1200px;
    height: 960px;
    display: flex;
    flex-direction: column;
    align-items: center;
    justify-content: center;
    gap: 60px;
  }
  .card {
    position: relative;
    width: 620px;
    height: 354px;
    box-shadow: 0 6px 18px rgba(0, 0, 0, 0.18);
  }
  .card--back { background: var(--card-yellow); color: var(--ink); }
  .card--front { background: var(--card-dark); }

  .identity {
    position: absolute;
    left: 40px;
    top: 46px;
    width: 320px;
    padding-bottom: 8px;
    border-bottom: 2px solid var(--ink);
    white-space: nowrap;
  }
  .identity__name { font-size: 30px; letter-spacing: 0.5px; }
  .identity__role { font-size: 17px; margin-left: 4px; }

  .contact {
    position: absolute;
    left: 40px;
    top: 124px;
    list-style: none;
    font-size: 19px;
    line-height: 26px;
  }
  .contact__label { display: inline-block; width: 34px; }

  .address {
    position: absolute;
    left: 40px;
    top: 216px;
    font-size: 19px;
    line-height: 25px;
    font-style: normal;
  }

  .brand {
    position: absolute;
    right: 32px;
    bottom: 30px;
    display: flex;
    align-items: center;
    gap: 12px;
    font-size: 28px;
    font-weight: 700;
    white-space: nowrap;
  }
  .brand--white { color: var(--white); }
  .brand--yellow { color: var(--accent-yellow); }
  .brand__dot {
    width: 26px;
    height: 26px;
    border-radius: 50%;
    background: var(--accent-yellow);
  }
</style>
</head>
<body>
<main class="sheet">
  <section class="card card--back" aria-label="Card back with contact details">
    <header class="identity">
      <span class="identity__name">JORDAN REYES</span>
      <span class="identity__role">Managing Partner</span>
    </header>
    <ul class="contact">
      <li><span class="contact__label">t</span>(480) 555-0147</li>
      <li><span class="contact__label">e</span>name@kestrelworks.com</li>
      <li><span class="contact__label">w</span>www.kestrelworks.com</li>
    </ul>
    <address class="address">
      1750 North Alder Creek Road,<br>
      Suite 410, Mesa Verde,<br>
      Arizona 85099
    </address>
    <div class="brand brand--white">The Kestrel Works</div>
  </section>

  <section class="card card--front" aria-label="Card front">
    <div class="brand brand--yellow">
      <span class="brand__dot"></span>
      The Kestrel Works
    </div>
  </section>
</main>
</body>
</html>
```